8x8 Social Media Ad - Brant Summit Expo

Attention Real Estate Agents
Please join us for our
Quarterly Real Estate Training Expo
The 2nd Saturday of February, May, August and November
Our Next Training Expo is _________________________________
From 9 am to 1 pm
at
Halvorne Suites Millbrook Court
4817 Copper Willow Lane, Dunmere, MD 20588
Scheduled Speakers
9:00 am - Marcus Pellington - Orientation
9:30 am - Derrin Oakfield - Multiple Income Streams / Crest Program
10:00 am - Talia Brennick - Marketing though Social Media
10:45 am - Rex Dunmore - Generating Business through Ru-Plaza
11:30 am - Kemi Adeyoro - Real Estate Investing
12:15 pm - Gregor Tamsey - (Main Speaker) Training Topic TBA
For more information call Marcus Pellington at (240) 555-0183 or email mpellington@brantsummithomes.example

```html
<!DOCTYPE html>
<html lang="en">
<head>
<meta charset="utf-8">
<title>Brant Summit Expo – Quarterly Real Estate Training Expo</title>
<link rel="stylesheet" href="https://fonts.googleapis.com/css2?family=Montserrat:ital,wght@0,400;0,500;0,600;0,700;0,800;1,300;1,400;1,700;1,800;1,900&display=swap">
<style>
  :root {
    --teal-light: #14908f;
    --teal-mid: #0d7475;
    --teal-dark: #075859;
    --teal-panel: #0a6364;
    --teal-band: #179c9b;
    --cyan: #3fe3da;
    --yellow: #ffe800;
    --white: #ffffff;
    --ink: #0a5a5c;
  }
  * { margin: 0; padding: 0; box-sizing: border-box; }
  html, body { width: 1200px; height: 1200px; overflow: hidden; }
  body { font-family: "Montserrat", Arial, sans-serif; color: var(--white); }

  .ad {
    position: relative;
    width: 1200px;
    height: 1200px;
    overflow: hidden;
    background: linear-gradient(160deg, var(--teal-mid) 0%, var(--teal-dark) 45%, var(--teal-light) 100%);
  }
  .ad__shade {
    position: absolute;
    left: 0; top: 700px;
    width: 760px; height: 500px;
    background: linear-gradient(180deg, rgba(30,170,168,0.35), rgba(30,170,168,0));
  }

  .brand {
    position: absolute;
    left: 0; top: 0;
    width: 354px; height: 142px;
    background: var(--white);
    border-bottom-right-radius: 40px;
    display: flex; align-items: center; justify-content: center; gap: 12px;
  }
  .brand__mark { width: 22px; height: 22px; background: var(--ink); }
  .brand__name { font-weight: 800; font-size: 34px; color: var(--ink); letter-spacing: 1px; }

  .speakers-panel {
    position: absolute;
    left: 750px; top: 54px;
    width: 450px; height: 1040px;
    background: var(--teal-panel);
    border-radius: 40px 0 0 40px;
  }
  .speakers-title {
    position: absolute;
    left: 690px; top: 78px;
    width: 474px; height: 60px;
    background: var(--teal-band);
    clip-path: polygon(3% 0, 100% 0, 97% 100%, 0 100%);
    display: flex; align-items: center; justify-content: center;
    font-size: 31px; font-weight: 500; letter-spacing: 1px;
  }
  .speakers-title strong { color: var(--cyan); font-weight: 800; margin-left: 10px; }

  .headline { position: absolute; left: 0; width: 660px; text-align: center; }
  .headline--attention { top: 176px; font-size: 55px; line-height: 56px; font-style: italic; font-weight: 300; }
  .headline--attention strong { display: block; font-weight: 800; }

  .invite {
    position: absolute;
    left: 36px; top: 318px;
    width: 588px; height: 70px;
    background: var(--yellow);
    clip-path: polygon(4% 0, 100% 0, 96% 100%, 0 100%);
    color: var(--ink);
    display: flex; align-items: center; justify-content: center;
    font-size: 31px; font-weight: 500;
  }
  .invite strong { font-weight: 800; font-style: italic; margin-left: 10px; }

  .headline--event { top: 430px; font-size: 64px; line-height: 62px; font-style: italic; font-weight: 300; }
  .headline--event strong { font-weight: 800; }
  .headline--event .hl { color: var(--yellow); font-weight: 800; display: block; }

  .schedule { position: absolute; left: 0; top: 722px; width: 660px; text-align: center; font-size: 36px; line-height: 42px; }
  .schedule__days { font-weight: 800; }
  .schedule__next { font-weight: 500; }
  .schedule__time { color: var(--yellow); font-weight: 800; }

  .venue { position: absolute; left: 76px; top: 950px; width: 520px; display: flex; gap: 18px; }
  .venue__pin { width: 34px; height: 46px; flex: none; margin-top: 10px; }
  .venue__text { font-size: 24px; line-height: 29px; font-weight: 500; }

  .speaker { position: absolute; left: 676px; width: 520px; height: 142px; }
  .speaker__photo {
    position: absolute; left: 0; top: 0;
    width: 142px; height: 142px; border-radius: 50%;
    background: var(--cyan);
    padding: 6px;
  }
  .speaker__photo span {
    display: block; width: 100%; height: 100%; border-radius: 50%;
    background: radial-gradient(circle at 50% 40%, #8a6a55 0%, #4a3a33 55%, #1f2a2e 100%);
  }
  .speaker__info { position: absolute; left: 162px; top: 16px; }
  .speaker__time { font-size: 32px; font-style: italic; font-weight: 400; line-height: 36px; }
  .speaker__name { font-size: 25px; font-weight: 800; color: var(--cyan); line-height: 32px; margin-top: 4px; }
  .speaker__topic { font-size: 17px; font-weight: 700; line-height: 20px; text-transform: uppercase; }

  .contact { position: absolute; top: 1120px; left: 0; width: 1200px; height: 80px; }
  .contact__call { position: absolute; left: 26px; top: 20px; font-size: 17px; line-height: 18px; font-weight: 500; }
  .contact__phone { position: absolute; left: 306px; top: 22px; display: flex; align-items: center; gap: 6px; font-size: 35px; font-weight: 800; }
  .contact__phone svg { width: 34px; height: 34px; }
  .contact__email { position: absolute; left: 650px; width: 540px; top: 2px; text-align: center; font-size: 25px; font-weight: 500; line-height: 34px; }
  .contact__email span { display: block; font-size: 21px; }
</style>
</head>
<body>
<main class="ad">
  <div class="ad__shade"></div>

  <div class="brand">
    <span class="brand__mark"></span>
    <span class="brand__name">BRANT SUMMIT</span>
  </div>

  <div class="speakers-panel"></div>
  <div class="speakers-title">SCHEDULED<strong>SPEAKERS</strong></div>

  <h1 class="headline headline--attention">ATTENTION REAL<strong>ESTATE AGENTS</strong></h1>

  <div class="invite">PLEASE JOIN<strong>US FOR OUR</strong></div>

  <h2 class="headline headline--event">QUARTERLY<br>REAL <strong>ESTATE</strong><span class="hl">TRAINING</span><span class="hl">EXPO</span></h2>

  <div class="schedule">
    <div class="schedule__days">THE 2ND SATURDAY OF<br>FEBRUARY, MAY, AUGUST<br>AND NOVEMBER</div>
    <div class="schedule__next">OUR NEXT TRAINING EXPO</div>
    <div class="schedule__time">IS FROM 9 AM TO 1 PM</div>
  </div>

  <div class="venue">
    <svg class="venue__pin" viewBox="0 0 34 46" aria-hidden="true">
      <path d="M17 0C7.6 0 0 7.6 0 17c0 12.5 17 29 17 29s17-16.5 17-29C34 7.6 26.4 0 17 0z" fill="#fff"/>
      <circle cx="17" cy="17" r="6.5" fill="#0d7475"/>
    </svg>
    <p class="venue__text">AT HALVORNE SUITES MILLBROOK COURT 4817 COPPER WILLOW LANE, DUNMERE, MD 20588.</p>
  </div>

  <section class="speaker" style="top:171px">
    <div class="speaker__photo"><span role="img" aria-label="Portrait photo of speaker Marcus Pellington"></span></div>
    <div class="speaker__info"><div class="speaker__time">9:00 AM</div><div class="speaker__name">MARCUS PELLINGTON</div><div class="speaker__topic">Orientation</div></div>
  </section>
  <section class="speaker" style="top:323px">
    <div class="speaker__photo"><span role="img" aria-label="Portrait photo of speaker Derrin Oakfield"></span></div>
    <div class="speaker__info"><div class="speaker__time">9:30 AM</div><div class="speaker__name">DERRIN OAKFIELD</div><div class="speaker__topic">Multiple income<br>streams / Crest program</div></div>
  </section>
  <section class="speaker" style="top:475px">
    <div class="speaker__photo"><span role="img" aria-label="Portrait photo of speaker Talia Brennick"></span></div>
    <div class="speaker__info"><div class="speaker__time">10:00 AM</div><div class="speaker__name">TALIA BRENNICK</div><div class="speaker__topic">Marketing<br>though social media</div></div>
  </section>
  <section class="speaker" style="top:627px">
    <div class="speaker__photo"><span role="img" aria-label="Portrait photo of speaker Rex Dunmore"></span></div>
    <div class="speaker__info"><div class="speaker__time">10:45 AM</div><div class="speaker__name">REX DUNMORE</div><div class="speaker__topic">Generating business<br>through Ru-Plaza</div></div>
  </section>
  <section class="speaker" style="top:777px">
    <div class="speaker__photo"><span role="img" aria-label="Portrait photo of speaker Kemi Adeyoro"></span></div>
    <div class="speaker__info"><div class="speaker__time">11:30 AM</div><div class="speaker__name">KEMI ADEYORO</div><div class="speaker__topic">Real estate investing</div></div>
  </section>
  <section class="speaker" style="top:927px">
    <div class="speaker__photo"><span role="img" aria-label="Portrait photo of main speaker Gregor Tamsey"></span></div>
    <div class="speaker__info"><div class="speaker__time">12:15 PM</div><div class="speaker__name">GREGOR TAMSEY</div><div class="speaker__topic">(Main speaker)<br>Training topic TBA</div></div>
  </section>

  <footer class="contact">
    <p class="contact__call">FOR MORE INFORMATION<br>CALL MARCUS PELLINGTON AT</p>
    <p class="contact__phone">
      <svg viewBox="0 0 34 34" aria-hidden="true">
        <circle cx="17" cy="17" r="17" fill="#fff"/>
        <path d="M11.5 8.5l3 3.4-1.7 2.3c1 2.3 2.8 4.2 5.1 5.2l2.3-1.7 3.4 3-1.6 3.3c-6.8-.4-12.8-6.4-13.2-13.2z" fill="#0d7475"/>
      </svg>(240) 555-0183
    </p>
    <p class="contact__email">OR EMAIL<span>MPELLINGTON@BRANTSUMMITHOMES.EXAMPLE</span></p>
  </footer>
</main>
</body>
</html>
```